Event Website Design

We need a new website design for an events driven website. The domain for this site is http://brackmoorhalls.co.uk. The site is up and running but needs a new fresh, modern look.
I've attached a Balamiq Mockup for the layout of the home page. Also attached is a png of the logo.
Key colours for the site are 0f7e6a, 35bde, d57835 & 373737.
Font to use is Proxima Nova
Width of the site should be 1200px
The design should be contemporary with minimal clutter.
Websites to references are…
http://vorpin.london/
http://www.darvushall.co.uk/
These are just guidelines, please feel free to use you own creative judgment.
The selected design file needs to be supplied as an editable PSD.
Reason: I've submitted 5 designs to the client, who will select the one they want. I will then choose that design. So please be patient as I'm waiting for a decision from my client.
Industry/Entity Type
Events
Number of Pages Required
1 page
Look and feel
Each slider illustrates characteristics of the customer's brand and the style your logo design should communicate.

```html
<!DOCTYPE html>
<html lang="en">
<head>
<meta charset="utf-8">
<title>Brackmoor Halls — Home</title>
<link href="https://fonts.googleapis.com/css2?family=Open+Sans:wght@400;600;700&display=swap" rel="stylesheet">
<style>
:root{
  --green:#0f7e6a;
  --blue:#1359c9;
  --orange:#d57835;
  --dark:#373737;
  --darker:#2b2b2b;
  --text:#444;
  --muted:#666;
  --white:#fff;
  --line:#e4e4e4;
}
*{box-sizing:border-box;margin:0;padding:0}
html,body{width:1200px;height:2206px;overflow:hidden}
body{font-family:"Open Sans",Arial,sans-serif;color:var(--text);background:var(--white);position:relative}
.abs{position:absolute}
/* header */
.header{position:absolute;left:0;top:0;width:1200px;height:125px;background:var(--dark)}
.brand{position:absolute;left:0;top:0;width:262px;height:125px;background:var(--darker);display:flex;align-items:center;justify-content:center;gap:10px}
.brand-mark{width:14px;height:14px;background:var(--green)}
.brand-name{color:var(--white);font-weight:700;font-size:22px;letter-spacing:1px}
.utility{position:absolute;left:262px;top:0;width:938px;height:34px;background:var(--green);display:flex;justify-content:flex-end;align-items:center;gap:36px;padding-right:32px}
.utility a{color:var(--white);font-size:11px;text-decoration:none;display:flex;align-items:center;gap:7px;text-transform:uppercase}
.utility svg{width:14px;height:14px;stroke:#fff;fill:none;stroke-width:1.5}
.tagline{left:288px;top:56px;color:var(--white)}
.tagline strong{display:block;font-size:15px;font-weight:700}
.tagline span{display:block;font-size:11.5px;margin-top:4px}
.boxoffice{left:590px;top:54px;display:flex;gap:16px;color:var(--white)}
.boxoffice svg{width:38px;height:42px;stroke:#9a9a9a;fill:none;stroke-width:2}
.boxoffice strong{display:block;font-size:15px;font-weight:700}
.boxoffice span{display:block;font-size:12px;margin-top:4px}
.search{left:801px;top:62px;width:236px;height:32px;border:1px solid #555;background:#333;display:flex;align-items:center;justify-content:space-between;padding-left:14px;color:#888;font-size:11px}
.search i{width:32px;height:30px;border-left:1px solid #555;display:flex;align-items:center;justify-content:center}
.search svg{width:14px;height:14px;stroke:#888;fill:none;stroke-width:1.6}
.social{position:absolute;top:62px;width:32px;height:32px;border:1px solid #555;display:flex;align-items:center;justify-content:center}
.social .dot{width:10px;height:10px;background:#888}
.social svg{width:14px;height:14px;stroke:#888;fill:none;stroke-width:1.5}
/* nav */
.nav{position:absolute;left:0;top:125px;width:1200px;height:44px;background:var(--white);border-bottom:1px solid var(--line);display:flex;justify-content:space-between;align-items:center;padding:0 104px 0 103px}
.nav a{font-size:11px;color:#333;text-decoration:none;text-transform:uppercase}
/* hero */
.hero{position:absolute;left:0;top:169px;width:1200px;height:527px;background:linear-gradient(100deg,#2a1c16 0%,#5a4030 40%,#6b5042 60%,#3a2a26 85%,#1f1a1c 100%)}
.hero-shade{position:absolute;inset:0;background:linear-gradient(90deg,rgba(0,0,0,.45),rgba(0,0,0,0) 60%)}
.hero-title{left:99px;top:218px;width:480px;color:var(--white);font-size:24px;font-weight:700;line-height:35px;text-transform:uppercase}
.date-badge{background:var(--orange);color:var(--white);font-size:11px;padding:6px 12px;text-transform:uppercase}
.hero-date{left:99px;top:300px}
.hero-copy{left:101px;top:343px;width:480px;color:var(--white);font-size:12.5px;line-height:20px;text-transform:uppercase}
.btn-ghost{display:inline-flex;align-items:center;justify-content:space-between;width:85px;height:31px;border:1px solid #fff;color:#fff;font-size:10px;padding:0 14px;text-transform:uppercase}
.hero-actions{left:102px;top:404px;display:flex;gap:10px}
.dots{left:570px;top:499px;display:flex;gap:6px}
.dots i{width:9px;height:9px;border-radius:50%;background:rgba(255,255,255,.5)}
.dots i:first-child{background:#fff}
/* tiles */
.tile{position:absolute;top:712px;width:265px;height:222px}
.tile-title{position:absolute;left:26px;top:112px;color:#fff;font-weight:700;font-size:15px;text-transform:uppercase}
.tile-date{position:absolute;left:26px;top:135px;color:#fff;font-size:10px;text-transform:uppercase}
.tile-actions{position:absolute;left:26px;top:168px;display:flex;gap:8px}
/* news */
.section-title{left:48px;top:985px;font-size:21px;font-weight:600;color:var(--dark);text-transform:uppercase}
.btn-orange{left:340px;top:987px;width:100px;height:25px;background:var(--orange);color:#fff;font-size:10px;display:flex;align-items:center;justify-content:center;text-transform:uppercase}
.news{position:absolute;top:1060px;width:340px}
.news-date{position:absolute;left:0;top:0;width:46px;height:65px;background:var(--blue);color:#fff;text-align:center}
.news-date b{display:block;font-size:16px;line-height:22px;margin-top:3px}
.news-date span{display:block;font-size:12px}
.news-date small{display:block;font-size:8px;margin-top:5px;text-transform:uppercase}
.news h3{position:absolute;left:68px;top:0;width:270px;font-size:12.5px;font-weight:700;color:var(--dark);line-height:21px;text-transform:uppercase}
.news p{position:absolute;left:68px;top:44px;width:272px;font-size:12.5px;line-height:22px;color:#555}
.btn-more{position:absolute;left:68px;top:125px;width:48px;height:18px;border:1px solid var(--orange);color:var(--orange);font-size:8.5px;display:flex;align-items:center;justify-content:center}
/* features */
.feature{position:absolute;top:1251px;width:350px;height:274px;color:#fff;text-align:center}
.feature svg{position:absolute;left:147px;top:70px;width:56px;height:56px;stroke:#fff;fill:none;stroke-width:2}
.feature h4{position:absolute;left:0;right:0;top:131px;font-size:16px;font-weight:700;text-transform:uppercase}
.feature .btn-small{position:absolute;left:142px;top:168px;width:66px;height:25px;border:1px solid #fff;font-size:10px;display:flex;align-items:center;justify-content:center}
/* sports */
.sports{position:absolute;left:0;top:1548px;width:1200px;height:392px;background:linear-gradient(100deg,#2a2826 0%,#6b625c 35%,#8a8580 55%,#5e5450 75%,#2c2a2a 100%);text-align:center;color:#fff}
.sports::after{content:"";position:absolute;inset:0;background:rgba(0,0,0,.25)}
.sports-inner{position:absolute;left:0;right:0;top:148px;z-index:1}
.sports h2{font-size:32px;font-weight:700;text-transform:uppercase}
.sports p{font-size:16px;margin-top:6px}
/* footer */
.footer-col{position:absolute;top:1985px}
.footer-col h5{font-size:15px;font-weight:600;color:var(--dark);text-transform:uppercase;margin-bottom:14px}
.footer-col li{list-style:none;font-size:10px;line-height:22px;color:#444;text-transform:uppercase}
.footer-brand{left:915px;top:2018px;display:flex;align-items:center;gap:10px}
.footer-brand .brand-mark{width:14px;height:14px}
.footer-brand .brand-name{color:#555;font-size:22px}
.copyright{left:0;width:1200px;top:2166px;text-align:center;font-size:10px;color:#444;text-transform:uppercase}
</style>
</head>
<body>

<header class="header">
  <div class="brand"><span class="brand-mark"></span><span class="brand-name">BRACKMOOR HALLS</span></div>
  <nav class="utility">
    <a href="#"><svg viewBox="0 0 16 16"><rect x="2" y="6" width="12" height="8"/><rect x="1" y="4" width="14" height="3"/><path d="M8 4v10"/></svg>Gift voucher</a>
    <a href="#"><svg viewBox="0 0 16 16"><rect x="1" y="3" width="14" height="10"/><path d="M1 3l7 6 7-6"/></svg>Join our mailing list</a>
    <a href="#"><svg viewBox="0 0 16 16"><circle cx="8" cy="8" r="3"/><circle cx="8" cy="8" r="6.5" stroke-dasharray="3 2"/></svg>My account</a>
    <a href="#"><svg viewBox="0 0 16 16"><path d="M2 5h12l-1 10H3z"/><path d="M5 5V3a3 3 0 016 0v2"/></svg>Basket</a>
    <a href="#"><svg viewBox="0 0 16 16"><path d="M13 9v5H2V3h5"/><path d="M7 10l1-3 6-6 2 2-6 6z"/></svg>Register</a>
  </nav>
  <div class="abs tagline"><strong>SOMERSET'S PREMIER</strong><span>ENTERTAINMENT AND SPORTING CENTRE</span></div>
  <div class="abs boxoffice">
    <svg viewBox="0 0 38 42"><path d="M3 16l16-12 16 12v22H3z"/><path d="M3 16l16 12 16-12"/><rect x="10" y="10" width="18" height="12"/></svg>
    <div><strong>BOX OFFICE</strong><span>07700 900 418</span></div>
  </div>
  <div class="abs search">Search<i><svg viewBox="0 0 16 16"><circle cx="7" cy="7" r="5"/><path d="M11 11l4 4"/></svg></i></div>
  <div class="social" style="left:1050px"><span class="dot"></span></div>
  <div class="social" style="left:1097px"><span class="dot"></span></div>
  <div class="social" style="left:1144px"><svg viewBox="0 0 16 16"><rect x="2" y="3" width="12" height="11"/><path d="M2 6h12M5 1v3M11 1v3"/></svg></div>
</header>

<nav class="nav">
  <a href="#">What's on</a>
  <a href="#">Conferencing and events</a>
  <a href="#">Sports &amp; leisure</a>
  <a href="#">Lantern Theatre</a>
  <a href="#">Plan your visit</a>
  <a href="#">News</a>
  <a href="#">Discover more</a>
  <a href="#">Contact us</a>
</nav>

<section class="hero" role="img" aria-label="Photo of friends laughing over dinner and wine">
  <div class="hero-shade"></div>
  <h1 class="abs hero-title">Dieter Falkmann: Lowersaxony is not an option</h1>
  <div class="abs hero-date date-badge">Sat 27 May 2017</div>
  <p class="abs hero-copy">Join German comedy ambassador Dieter Falkmann for an evening of Teutonic jolliness at its best.</p>
  <div class="abs hero-actions"><span class="btn-ghost">More <b>›</b></span><span class="btn-ghost">Book <b>›</b></span></div>
  <div class="abs dots"><i></i><i></i><i></i><i></i></div>
</section>

<div class="tile" style="left:48px;background:linear-gradient(135deg,#4a2038,#7a3a4a 50%,#3a1a2a)" role="img" aria-label="Photo of a party with confetti">
  <div class="tile-title">Martin's Party</div>
  <div class="tile-date">Mon 7 Jan</div>
  <div class="tile-actions"><span class="btn-ghost">More <b>›</b></span><span class="btn-ghost">Book <b>›</b></span></div>
</div>
<div class="tile" style="left:328px;background:linear-gradient(135deg,#d8d4cc,#b89a88 50%,#8a6a66)" role="img" aria-label="Photo of friends sharing pizza"></div>
<div class="tile" style="left:608px;background:linear-gradient(135deg,#3a1028,#a02a5a 50%,#4a1030)" role="img" aria-label="Photo of a crowd dancing at a concert"></div>
<div class="tile" style="left:888px;background:linear-gradient(135deg,#2a2a2e,#4a3a38 50%,#1e1e22)" role="img" aria-label="Photo of friends celebrating with drinks"></div>

<h2 class="abs section-title">Latest from Brackmoor</h2>
<div class="abs btn-orange">See all news</div>

<article class="news" style="left:48px">
  <div class="news-date"><b>21</b><span>2016</span><small>March</small></div>
  <h3>Dieter Falkmann: Lowersaxony is not an option</h3>
  <p>Lorem Ipsum is simply dummy text of the printing and typesetting industry. Lorem Ipsum has been the industry...</p>
  <span class="btn-more">MORE</span>
</article>
<article class="news" style="left:435px">
  <div class="news-date"><b>21</b><span>2016</span><small>March</small></div>
  <h3>Dieter Falkmann: Lowersaxony is not an option</h3>
  <p>Lorem Ipsum is simply dummy text of the printing and typesetting industry. Lorem Ipsum has been the industry...</p>
  <span class="btn-more">MORE</span>
</article>
<article class="news" style="left:819px">
  <div class="news-date"><b>21</b><span>2016</span><small>March</small></div>
  <h3>Dieter Falkmann: Lowersaxony is not an option</h3>
  <p>Lorem Ipsum is simply dummy text of the printing and typesetting industry. Lorem Ipsum has been the industry...</p>
  <span class="btn-more">MORE</span>
</article>

<div class="feature" style="left:48px;background:linear-gradient(135deg,#5a2a22,#3a2a30 50%,#1e2a4a)" role="img" aria-label="Photo of a speaker presenting at a conference">
  <svg viewBox="0 0 56 56"><circle cx="22" cy="18" r="9"/><path d="M6 46c0-10 7-16 16-16s16 6 16 16z"/><circle cx="36" cy="16" r="8"/><path d="M38 28c8 1 13 7 13 15h-9"/></svg>
  <h4>Conferences &amp; Events</h4><span class="btn-small">MORE</span>
</div>
<div class="feature" style="left:425px;background:linear-gradient(135deg,#4a1a14,#6a2a1e 50%,#3a120e)" role="img" aria-label="Photo of guests raising glasses in a toast">
  <svg viewBox="0 0 56 56"><path d="M8 10h16l-2 14a6 6 0 01-12 0z"/><path d="M16 30v14M10 44h12"/><path d="M32 10h16l-2 14a6 6 0 01-12 0z"/><path d="M40 30v14M34 44h12"/></svg>
  <h4>Parties at Brackmoor</h4><span class="btn-small">MORE</span>
</div>
<div class="feature" style="left:801px;background:linear-gradient(180deg,#3a2a30,#6a4a44 55%,#2a2020)" role="img" aria-label="Photo of people on a beach at dusk with fireworks">
  <svg viewBox="0 0 56 56"><path d="M6 8h30v20H18l-8 7v-7H6z"/><path d="M40 18h10v20h-4v7l-8-7H24v-6"/></svg>
  <h4>Co-working hub</h4><span class="btn-small">MORE</span>
</div>

<section class="sports" role="img" aria-label="Photo of people training in a fitness class">
  <div class="sports-inner">
    <h2>Sports &amp; Leisure</h2>
    <p>For those wanting more information about the Sports &amp; Fitness Centre give their page a like!</p>
  </div>
</section>

<footer>
  <div class="footer-col" style="left:107px">
    <h5>Postal address</h5>
    <ul><li>Brackmoor Entertainment Venue</li><li>Harrowgate Close</li><li>Brackmoor</li><li>Somerset</li><li>BX20 4QT</li></ul>
  </div>
  <div class="footer-col" style="left:432px">
    <h5>Events</h5>
    <ul><li>What's on</li><li>Conferencing &amp; events</li><li>Sports &amp; leisure</li><li>Lantern Theater</li></ul>
  </div>
  <div class="footer-col" style="left:699px">
    <h5>Others</h5>
    <ul><li>Plan your visit</li><li>News</li><li>Discover more</li><li>Contact us</li></ul>
  </div>
  <div class="abs footer-brand"><span class="brand-mark"></span><span class="brand-name">BRACKMOOR HALLS</span></div>
  <div class="abs copyright">Copyright © 2016. Brackmoor Halls. All rights reserved</div>
</footer>

</body>
</html>
```